Business Card Design Project

Business and Appointment Card for Medical Practice. On back of card we would like to have: blank line for patient name, Mon-Fri each with a check box next to the day, blank line for appointment date, blank line for appointment time, with option to circle am or pm.

Target Market(s)

Professional Business Associates, as well as function as patient appointment cards (on back side of card)

Industry/Entity Type

Business

Colors

Designer to choose colors to be used in the design.

```html
<!DOCTYPE html>
<html lang="en">
<head>
<meta charset="utf-8">
<title>Linden Grove Medical Associates – Business and Appointment Card</title>
<link href="https://fonts.googleapis.com/css2?family=Open+Sans:wght@400;600&display=swap" rel="stylesheet">
<style>
  :root {
    --bg: #e4e4e4;
    --green: #0f7a3e;
    --green-deep: #0a6431;
    --red: #a8161c;
    --red-text: #c8232a;
    --white: #ffffff;
    --grey-text: #e9f2ec;
    --field: #ffffff;
  }
  * { box-sizing: border-box; margin: 0; padding: 0; }
  html, body { width: 1200px; height: 900px; overflow: hidden; }
  body {
    background: var(--bg);
    font-family: "Open Sans", Arial, sans-serif;
    display: flex;
    align-items: center;
    justify-content: center;
    gap: 50px;
  }
  .card {
    position: relative;
    width: 540px;
    height: 310px;
    border-radius: 24px;
    overflow: hidden;
    box-shadow: 0 10px 24px rgba(0,0,0,0.18);
  }

  /* Front */
  .card-front { background: linear-gradient(180deg, var(--green) 0%, var(--green-deep) 100%); }
  .front-top {
    position: absolute; inset: 0 0 auto 0; height: 168px;
    background: var(--white);
    display: flex; align-items: center; justify-content: center; gap: 14px;
  }
  .brand-dot {
    width: 46px; height: 46px; border-radius: 50%;
    border: 3px solid var(--green);
  }
  .brand-name {
    color: var(--green);
    font-weight: 600;
    font-size: 25px;
    line-height: 1.15;
    text-align: left;
  }
  .front-stripe {
    position: absolute; left: 0; right: 0; top: 168px; height: 9px;
    background: var(--red);
  }
  .front-bottom {
    position: absolute; left: 0; right: 0; top: 177px; bottom: 0;
    display: flex; align-items: center;
  }
  .person {
    width: 220px; text-align: right; padding-right: 22px;
  }
  .person-name { color: var(--red-text); font-size: 16px; }
  .person-role { color: var(--grey-text); font-size: 12px; margin-top: 2px; }
  .divider { width: 1px; height: 76px; background: rgba(255,255,255,0.6); }
  .contacts { list-style: none; padding-left: 16px; }
  .contacts li {
    display: flex; align-items: center; gap: 7px;
    color: var(--white); font-size: 15px; line-height: 22px;
  }
  .contacts svg { width: 13px; height: 13px; flex: none; }

  /* Back */
  .card-back { background: linear-gradient(180deg, var(--green) 0%, var(--green-deep) 100%); }
  .back-mark {
    position: absolute; left: 100px; top: 10px; width: 340px; height: 340px;
    border-radius: 50%; border: 4px solid rgba(0,0,0,0.08);
  }
  .appointment-title {
    position: absolute; top: 62px; left: 0; right: 0; text-align: center;
    color: var(--red-text); font-size: 16px;
  }
  .form { position: absolute; left: 30px; right: 18px; top: 100px; }
  .row { display: flex; align-items: center; height: 30px; margin-bottom: 12px; }
  .label { color: var(--white); font-size: 17px; width: 66px; }
  .field { background: var(--field); height: 27px; }
  .field-name { flex: 1; }
  .field-date, .field-time { width: 188px; }
  .days { display: flex; gap: 8px; margin-left: 10px; }
  .day { display: flex; align-items: center; gap: 3px; color: var(--white); font-size: 11px; }
  .box { width: 12px; height: 12px; background: var(--field); }
  .ampm { color: var(--white); font-size: 13px; margin-left: 10px; }
</style>
</head>
<body>
  <section class="card card-front">
    <div class="front-top">
      <span class="brand-dot"></span>
      <h1 class="brand-name">Linden Grove<br>Medical Associates</h1>
    </div>
    <div class="front-stripe"></div>
    <div class="front-bottom">
      <div class="person">
        <p class="person-name">Daniel Reyes</p>
        <p class="person-role">Manager</p>
      </div>
      <div class="divider"></div>
      <ul class="contacts">
        <li>
          <svg viewBox="0 0 16 16" aria-hidden="true"><path fill="#d9363d" d="M3 1l3 3-1.5 2a9 9 0 0 0 5.5 5.5L12 10l3 3-2 2C6 15 1 10 1 3z"/></svg>
          555-014-2290
        </li>
        <li>
          <svg viewBox="0 0 16 16" aria-hidden="true"><g fill="none" stroke="#d9363d" stroke-width="1.5"><circle cx="8" cy="8" r="6.5"/><ellipse cx="8" cy="8" rx="3" ry="6.5"/><path d="M1.5 8h13"/></g></svg>
          www.lindengrove.com
        </li>
        <li>
          <svg viewBox="0 0 16 16" aria-hidden="true"><g fill="none" stroke="#d9363d" stroke-width="1.5"><rect x="1.5" y="3.5" width="13" height="9"/><path d="M1.5 3.5l6.5 5 6.5-5"/></g></svg>
          info@lindengrove.com
        </li>
        <li>
          <svg viewBox="0 0 16 16" aria-hidden="true"><path fill="#d9363d" d="M8 1l7 6h-2v8H9.5v-5h-3v5H3V7H1z"/></svg>
          48 Harbor Lane Boston
        </li>
      </ul>
    </div>
  </section>

  <section class="card card-back">
    <div class="back-mark"></div>
    <h2 class="appointment-title">Appointment</h2>
    <div class="form">
      <div class="row">
        <span class="label">Name :</span>
        <span class="field field-name"></span>
      </div>
      <div class="row">
        <span class="label">Date &nbsp;:</span>
        <span class="field field-date"></span>
        <div class="days">
          <span class="day">Mon<span class="box"></span></span>
          <span class="day">Tue<span class="box"></span></span>
          <span class="day">Wed<span class="box"></span></span>
          <span class="day">Thu<span class="box"></span></span>
          <span class="day">Fri<span class="box"></span></span>
        </div>
      </div>
      <div class="row">
        <span class="label">Time &nbsp;:</span>
        <span class="field field-time"></span>
        <span class="ampm">am / pm</span>
      </div>
    </div>
  </section>
</body>
</html>
```